Cedar Brook Stables, LLC

Equestrian business card to promote equine retirement, farm sitting, short term board. Located in Aiken, SC.
Updates
Updated color schemes.
Contact Information for Business Card
Contact info, description of work.
Colors
0094D4
00A9DD
6FCCEA
C7EBF8
E9F6FB
59FF00
82FF00
B8FF75
E3FFCB
F4FFEA
F0912C
F2A743
F7CA91
FBE8D2
FDF5EE

```html
<!DOCTYPE html>
<html lang="en">
<head>
<meta charset="utf-8">
<title>Cedar Brook Stables – Business Card</title>
<link rel="stylesheet" href="https://fonts.googleapis.com/css2?family=Poppins:wght@400;500;600;700&display=swap">
<style>
  :root {
    --bg: #e9ebe9;
    --card-white: #ffffff;
    --card-black: #151617;
    --pattern-dark: #1d1e20;
    --pattern-light: #2c2d30;
    --green: #1b7a12;
    --green-dark: #136008;
    --ink: #2b2b2b;
    --rule: #9a9a9a;
    --sun: #f2a743;
    --white: #ffffff;
  }
  * { box-sizing: border-box; margin: 0; padding: 0; }
  html, body { width: 1200px; height: 1108px; overflow: hidden; }
  body {
    background: var(--bg);
    font-family: "Poppins", sans-serif;
    display: flex;
    align-items: center;
    justify-content: center;
    gap: 70px;
  }
  .card {
    width: 400px;
    height: 680px;
    border-radius: 22px;
    position: relative;
    overflow: hidden;
    box-shadow: 0 14px 34px rgba(0,0,0,.18);
  }
  /* Front */
  .card-front {
    background: var(--card-white);
    display: flex;
    flex-direction: column;
    align-items: center;
    text-align: center;
    padding: 0 40px;
  }
  .brand-mark {
    margin-top: 120px;
    display: flex;
    align-items: center;
    gap: 12px;
  }
  .brand-dot {
    width: 22px; height: 22px;
    border-radius: 50%;
    background: var(--sun);
    flex: none;
  }
  .brand-name {
    font-weight: 600;
    font-size: 21px;
    color: var(--ink);
    letter-spacing: .5px;
    text-transform: uppercase;
    line-height: 1.25;
  }
  .person-name {
    margin-top: 110px;
    font-weight: 700;
    font-size: 30px;
    color: var(--green);
    letter-spacing: .5px;
    text-transform: uppercase;
    line-height: 1;
  }
  .person-title {
    margin-top: 6px;
    font-size: 16px;
    color: var(--ink);
    letter-spacing: 1px;
    text-transform: uppercase;
  }
  .icon-rule {
    margin-top: 22px;
    width: 100%;
    display: flex;
    align-items: center;
    gap: 10px;
  }
  .icon-rule::before, .icon-rule::after {
    content: "";
    flex: 1;
    height: 1px;
    background: var(--rule);
  }
  .contact-icon {
    width: 30px; height: 30px;
    background: var(--green);
    border-radius: 3px;
    display: flex; align-items: center; justify-content: center;
  }
  .contact-icon svg { width: 18px; height: 18px; }
  .contact-list {
    list-style: none;
    margin-top: 14px;
    font-size: 17px;
    color: var(--ink);
    line-height: 1.5;
  }
  .address-rule {
    margin-top: 18px;
    width: 100%;
    height: 1px;
    background: var(--rule);
  }
  .address {
    margin-top: 16px;
    font-style: normal;
    font-size: 17px;
    color: var(--ink);
    line-height: 1.45;
  }
  /* Back */
  .card-back { background: var(--card-black); }
  .back-pattern {
    position: absolute; inset: 0;
    background: radial-gradient(ellipse at 65% 30%, var(--pattern-light), var(--pattern-dark) 60%, var(--card-black));
  }
  .back-content {
    position: absolute;
    left: 0; right: 0; bottom: 110px;
    display: flex; flex-direction: column; align-items: center;
  }
  .back-brand {
    display: flex; align-items: center; gap: 8px;
    font-weight: 600;
    font-size: 13px;
    color: var(--white);
    text-transform: uppercase;
    letter-spacing: .5px;
    margin-bottom: 40px;
  }
  .back-brand .brand-dot { width: 12px; height: 12px; }
  .services {
    list-style: none;
    text-align: center;
    color: var(--white);
    font-weight: 500;
    font-size: 19px;
    letter-spacing: .5px;
    line-height: 1.45;
    text-transform: uppercase;
  }
</style>
</head>
<body>

  <article class="card card-front">
    <div class="brand-mark">
      <span class="brand-dot"></span>
      <span class="brand-name">Cedar Brook Stables, LLC</span>
    </div>

    <h1 class="person-name">Daniel Hayes</h1>
    <p class="person-title">Managing Director</p>

    <div class="icon-rule">
      <span class="contact-icon">
        <svg viewBox="0 0 24 24" fill="none" stroke="#fff" stroke-width="2" stroke-linecap="round" stroke-linejoin="round">
          <path d="M5 4h4l2 5-2.5 1.5a11 11 0 0 0 5 5L15 13l5 2v4a2 2 0 0 1-2 2A16 16 0 0 1 3 6a2 2 0 0 1 2-2"/>
        </svg>
      </span>
      <span class="contact-icon">
        <svg viewBox="0 0 24 24" fill="none" stroke="#fff" stroke-width="2" stroke-linejoin="round">
          <rect x="3" y="5" width="18" height="14" rx="1"/>
          <path d="M3 6l9 7 9-7"/>
        </svg>
      </span>
      <span class="contact-icon">
        <svg viewBox="0 0 24 24" fill="none" stroke="#fff" stroke-width="2">
          <circle cx="12" cy="12" r="9"/>
          <path d="M3 12h18M12 3a14 14 0 0 1 0 18M12 3a14 14 0 0 0 0 18"/>
        </svg>
      </span>
    </div>

    <ul class="contact-list">
      <li>044-555 018 274</li>
      <li>info@cedarbrook.com</li>
      <li>www.cedarbrookstables.com</li>
    </ul>

    <div class="address-rule"></div>
    <address class="address">
      418 Brookline Road, Aiken<br>
      SC 29801, United States
    </address>
  </article>

  <article class="card card-back">
    <div class="back-pattern" role="img" aria-label="Repeating tone-on-tone pattern of the stable emblem in gloss black"></div>
    <div class="back-content">
      <div class="back-brand">
        <span class="brand-dot"></span>
        <span>Cedar Brook Stables, LLC</span>
      </div>
      <ul class="services">
        <li>Short Term Board</li>
        <li>Farm Sitting</li>
        <li>Equine Retirement</li>
      </ul>
    </div>
  </article>

</body>
</html>
```